Harbourline Electrical Solutions

On one side. LOGO (underneath:) Commercial Industrial Residential

- NAME & CONTACT DETAILS

Marcus T. Hollings
Project Manager

(Cell icon) (441) 555-0187
(Email icon) hlelectricalsolutions@mailvento.com
(Facebook & Instagram icons )@hlelectricalsolutions

Other side: LOGO - underneath ELECTRICAL CONSTRUCTION & MAINTENANCE . LED LIGHTING & AUTOMATION . LIFE SAFETY SYSTEMS (FIRE ALARM / SECURITY) . DATA & COMMUNICATION

```html
<!DOCTYPE html>
<html lang="en">
<head>
<meta charset="utf-8">
<title>Harbourline Electrical Solutions – Business Card</title>
<link href="https://fonts.googleapis.com/css2?family=Montserrat:wght@400;500;600;700&display=swap" rel="stylesheet">
<style>
  :root {
    --teal: #10566b;
    --ink: #3d3d3f;
    --paper: #ffffff;
    --backdrop: #1f1f21;
    --rule-grey: #555557;
  }
  * { margin: 0; padding: 0; box-sizing: border-box; }
  html, body {
    width: 1200px; height: 1200px; overflow: hidden;
    background: var(--backdrop);
    font-family: "Montserrat", Arial, sans-serif;
  }
  .card {
    position: absolute; left: 294px; width: 612px; height: 366px;
    background: var(--paper); overflow: hidden;
  }
  /* ---------- services side ---------- */
  .card--services { top: 208px; }
  .services-panel {
    position: absolute; left: 0; top: 0; width: 456px; height: 100%;
    background: var(--teal);
  }
  .service-list {
    position: absolute; left: 81px; top: 137px; list-style: none;
    color: var(--paper); font-weight: 500; font-size: 12.4px; line-height: 14.5px;
  }
  .service-list li { position: relative; padding-left: 9px; margin-bottom: 8px; }
  .service-list li::before {
    content: ""; position: absolute; left: 0; top: 4.5px;
    width: 4.5px; height: 4.5px; background: var(--paper);
  }
  .brand-strip {
    position: absolute; left: 456px; top: 0; width: 156px; height: 100%;
    display: flex; flex-direction: column; align-items: center; justify-content: center; gap: 18px;
  }
  .brand-strip__name {
    writing-mode: vertical-rl; transform: rotate(180deg);
    color: var(--teal); font-weight: 500; font-size: 17.5px;
    letter-spacing: 2.6px; line-height: 19px; text-align: left;
  }
  .brand-mark-square { width: 14px; height: 14px; background: var(--teal); }
  /* ---------- contact side ---------- */
  .card--contact { top: 630px; }
  .brand-lockup {
    position: absolute; left: 47px; top: 42px;
    display: flex; align-items: center; gap: 12px;
  }
  .brand-lockup__square { width: 30px; height: 30px; background: var(--teal); }
  .brand-lockup__name {
    color: var(--teal); font-weight: 600; font-size: 15.5px;
    letter-spacing: 2.4px; line-height: 16.5px;
  }
  .sectors {
    position: absolute; left: 46px; top: 112px;
    font-size: 9.8px; font-weight: 500; letter-spacing: 2.4px; color: #222;
  }
  .sectors .divider { color: var(--teal); margin: 0 5px; font-weight: 600; }
  .person { position: absolute; left: 46px; top: 244px; }
  .person__name { color: var(--teal); font-weight: 700; font-size: 17px; letter-spacing: 0.2px; }
  .person__role { color: var(--ink); font-weight: 500; font-size: 11.5px; margin-top: 0; }
  .person__rule { width: 49px; height: 2px; background: var(--teal); margin-top: 8px; }
  .contact-line {
    position: absolute; left: 46px; display: flex; align-items: center; gap: 4px;
    color: var(--ink); font-size: 12.2px; letter-spacing: 0.3px;
  }
  .contact-line--phone { top: 301px; }
  .contact-line--email { top: 320px; }
  .contact-line--social { left: auto; right: 48px; top: 320px; gap: 6px; }
  .contact-icon { width: 12px; height: 12px; flex: none; }
  .social-dot {
    width: 12px; height: 12px; border: 1.2px solid var(--teal); border-radius: 50%;
  }
</style>
</head>
<body>
  <section class="card card--services">
    <div class="services-panel">
      <ul class="service-list">
        <li>ELECTRICAL CONSTRUCTION<br>&amp; MAINTENANCE</li>
        <li>LED LIGHTING &amp; AUTOMATION</li>
        <li>LIFE SAFETY SYSTEMS<br>(FIRE ALARM / SECURITY)</li>
        <li>DATA &amp; COMMUNICATION</li>
      </ul>
    </div>
    <div class="brand-strip">
      <div class="brand-strip__name">HARBOURLINE<br>ELECTRICAL<br>SOLUTIONS</div>
      <div class="brand-mark-square"></div>
    </div>
  </section>

  <section class="card card--contact">
    <div class="brand-lockup">
      <div class="brand-lockup__square"></div>
      <div class="brand-lockup__name">HARBOURLINE<br>ELECTRICAL<br>SOLUTIONS</div>
    </div>
    <div class="sectors">COMMERCIAL<span class="divider">|</span>INDUSTRIAL<span class="divider">|</span>RESIDENTIAL</div>

    <div class="person">
      <div class="person__name">MARCUS T. HOLLINGS</div>
      <div class="person__role">Project Manager</div>
      <div class="person__rule"></div>
    </div>

    <div class="contact-line contact-line--phone">
      <svg class="contact-icon" viewBox="0 0 12 12" aria-hidden="true">
        <circle cx="6" cy="6" r="5.4" fill="none" stroke="var(--teal)" stroke-width="1"/>
        <path d="M4 3.2l1 1.4-.6.7c.4.9 1 1.5 1.9 1.9l.7-.6 1.4 1-.6 1c-2.4-.3-4.2-2.1-4.5-4.5z" fill="var(--teal)"/>
      </svg>
      <span>(441) 555-0187</span>
    </div>
    <div class="contact-line contact-line--email">
      <svg class="contact-icon" viewBox="0 0 12 12" aria-hidden="true">
        <circle cx="6" cy="6" r="5.4" fill="none" stroke="var(--teal)" stroke-width="1"/>
        <rect x="3.3" y="4" width="5.4" height="4" fill="none" stroke="var(--teal)" stroke-width="0.9"/>
        <path d="M3.3 4l2.7 2.1L8.7 4" fill="none" stroke="var(--teal)" stroke-width="0.9"/>
      </svg>
      <span>hlelectricalsolutions@mailvento.com</span>
    </div>
    <div class="contact-line contact-line--social">
      <span class="social-dot"></span>
      <span>@hlelectricalsolutions</span>
    </div>
  </section>
</body>
</html>
```